Lanternfield Drinks business cards

We need a business card design for our new logo. The company is modern, progressive, professional, yet approachable. The key products are ready to drink bottles and cans of coffee based beverages.
These cards will be a critical part of the first impression made by our sales organization, business development team, and all external facing personnel.
Card can be a vertical or horizontal orientation.

Target Market(s)

Customers, suppliers, business partners

Industry/Entity Type

Business

Contact Information for Business Card

Business cards should feature Company Name and Logo.

Font styles to use
Serif

Colors

Designer to choose colors to be used in the design.

Requirements
Must have
• Strong readability of Name, phone #, mobile number and email address.
• Job title, website url, Street Address, and other details can be secondary level readability.
Nice to have
• High impact, simplistic quality design.
• Ok to utilize the 'H in the box' separate from the company name

```html
<!DOCTYPE html>
<html lang="en">
<head>
<meta charset="utf-8">
<title>Lanternfield Drinks business cards</title>
<link rel="stylesheet" href="https://fonts.googleapis.com/css2?family=Lato:wght@400;700&display=swap">
<style>
  :root {
    --backdrop: #3b3532;
    --card: #2a2627;
    --panel: #333031;
    --orange: #f15a2b;
    --white: #f4f1ee;
    --rule: #8a8482;
  }
  * { box-sizing: border-box; margin: 0; padding: 0; }
  html, body { width: 1200px; height: 844px; overflow: hidden; }
  body {
    background: var(--backdrop);
    font-family: "Lato", Arial, sans-serif;
    position: relative;
  }
  .card {
    position: absolute;
    top: 272px;
    width: 525px;
    height: 300px;
    background: var(--card);
    box-shadow: 0 8px 24px rgba(0,0,0,.45);
    overflow: hidden;
  }
  .card--contact { left: 45px; }
  .card--brand { left: 630px; }

  .band {
    position: absolute;
    left: 0; right: 0;
    height: 11px;
    background: var(--orange);
  }
  .band--top { top: 0; }
  .band--bottom { bottom: 0; }

  .contact-panel {
    position: absolute;
    left: 170px; top: 52px;
    width: 210px; height: 196px;
    background: var(--panel);
    padding: 14px 18px;
    color: var(--white);
    font-size: 12.5px;
    line-height: 1.3;
  }
  .contact-name {
    color: var(--orange);
    font-weight: 700;
    font-size: 17px;
    letter-spacing: .3px;
  }
  .contact-title {
    font-size: 11.5px;
    letter-spacing: .4px;
    padding-bottom: 7px;
    border-bottom: 1px solid var(--rule);
    margin-bottom: 8px;
  }
  .contact-lines { list-style: none; text-align: right; padding-right: 4px; }
  .contact-lines b { color: var(--orange); font-weight: 700; }
  .contact-address {
    margin-top: 8px;
    padding-top: 7px;
    border-top: 1px solid var(--rule);
    text-align: right;
    padding-right: 4px;
  }

  .edge-mark {
    position: absolute;
    width: 12px;
    background: var(--orange);
  }
  .edge-mark--left { left: 0; top: 128px; height: 42px; }
  .edge-mark--right { right: 0; top: 18px; height: 40px; }

  .brand-lockup {
    position: absolute;
    left: 0; right: 0; top: 70px;
    display: flex;
    flex-direction: column;
    align-items: center;
    gap: 22px;
  }
  .brand-square {
    width: 74px; height: 74px;
    border: 4px solid var(--orange);
  }
  .brand-name {
    color: var(--orange);
    font-weight: 700;
    font-size: 33px;
    letter-spacing: 1px;
    text-transform: uppercase;
  }
</style>
</head>
<body>
  <section class="card card--contact">
    <div class="band band--top"></div>
    <div class="contact-panel">
      <p class="contact-name">MARA ELLISON</p>
      <p class="contact-title">MANAGING DIRECTOR</p>
      <ul class="contact-lines">
        <li><b>P:</b> 444 555 2917</li>
        <li><b>M:</b> 888 555 7140</li>
        <li><b>E:</b> hello@lanternfield.com</li>
        <li><b>W:</b> www.lanternfield.com</li>
      </ul>
      <p class="contact-address">38, Millbrook Lane,<br>Harwell, 45190<br>Norland</p>
    </div>
    <div class="band band--bottom"></div>
  </section>

  <section class="card card--brand">
    <div class="edge-mark edge-mark--left"></div>
    <div class="edge-mark edge-mark--right"></div>
    <div class="brand-lockup">
      <div class="brand-square"></div>
      <p class="brand-name">Lanternfield Drinks</p>
    </div>
  </section>
</body>
</html>
```